Business Card Design (NEW FILES)

ATTENTION: New vector files are available. Please update your design to reflect/use the new (better resolution) logo images.

Seeking a unique and professional business card design for a commercial drone photography/videography business. The layout should feature
the logo (attached) and include the following information:
Owen Tarrick
614-502-7738
www.skylarkreelworks.example
NRD Certified Remote Pilot

Owen Tarrick

```html
<!DOCTYPE html>
<html lang="en">
<head>
<meta charset="utf-8">
<title>Skylark Reelworks – Business Card</title>
<link rel="stylesheet" href="https://fonts.googleapis.com/css2?family=Lato:wght@300;400;700;900&display=swap">
<style>
  :root {
    --backdrop: #8f8f8f;
    --navy: #03063a;
    --navy-back: #131a47;
    --orange: #ec8b55;
    --white: #ffffff;
    --ink: #15183f;
  }
  * { margin: 0; padding: 0; box-sizing: border-box; }
  html, body { width: 1200px; height: 1200px; overflow: hidden; }
  body {
    background: var(--backdrop);
    font-family: "Lato", sans-serif;
    position: relative;
  }
  .card {
    position: absolute;
    left: 281px;
    width: 642px;
    height: 366px;
    border-radius: 20px;
    overflow: hidden;
  }
  .card--front { top: 195px; background: var(--white); }
  .card--back { top: 639px; background: var(--navy-back); }
  .card__shapes { position: absolute; inset: 0; width: 100%; height: 100%; }

  .brand {
    position: absolute;
    display: flex;
    align-items: center;
    gap: 14px;
    font-weight: 300;
    line-height: 1;
    text-transform: uppercase;
  }
  .brand__dot { border-radius: 50%; background: var(--orange); flex: none; }
  .brand__name span { display: block; }

  .card--front .brand { left: 62px; top: 82px; color: var(--ink); font-size: 38px; letter-spacing: 1px; }
  .card--front .brand__dot { width: 22px; height: 22px; }
  .card--back .brand { left: 50%; top: 50%; transform: translate(-50%, -50%); color: var(--white); font-size: 48px; letter-spacing: 1.5px; }
  .card--back .brand__dot { width: 28px; height: 28px; }

  .contact { position: absolute; left: 63px; top: 212px; list-style: none; color: var(--ink); font-size: 15px; }
  .contact__item { display: flex; align-items: center; gap: 10px; height: 23px; }
  .contact__item:first-child { font-size: 16px; letter-spacing: 0.5px; }
  .contact__icon { width: 13px; height: 13px; flex: none; }

  .credentials { position: absolute; left: 63px; top: 266px; }
  .credentials__cert { color: var(--ink); font-weight: 700; font-size: 15px; }
  .credentials__insured { color: var(--orange); font-weight: 900; font-size: 16.5px; letter-spacing: 1px; margin-top: 6px; }

  .person { position: absolute; right: 44px; top: 276px; text-align: right; }
  .person__name { color: var(--white); font-weight: 900; font-size: 26px; letter-spacing: 0.3px; text-transform: uppercase; }
  .person__role { color: var(--orange); font-size: 17px; margin-top: 4px; }
</style>
</head>
<body>

<section class="card card--front" aria-label="Business card front">
  <svg class="card__shapes" viewBox="0 0 642 366" preserveAspectRatio="none" aria-hidden="true">
    <path d="M0 0 L150 0 C85 18 28 68 0 122 Z" fill="var(--orange)"/>
    <path d="M642 4 C540 180 350 352 90 366 L642 366 Z" fill="var(--navy)"/>
  </svg>

  <div class="brand">
    <div class="brand__name"><span>Skylark</span><span>Reelworks</span></div>
    <div class="brand__dot"></div>
  </div>

  <ul class="contact">
    <li class="contact__item">
      <svg class="contact__icon" viewBox="0 0 24 24" aria-hidden="true"><path fill="var(--orange)" d="M6.6 10.8a15.1 15.1 0 0 0 6.6 6.6l2.2-2.2a1 1 0 0 1 1-.25 11.4 11.4 0 0 0 3.6.57 1 1 0 0 1 1 1V20a1 1 0 0 1-1 1A17 17 0 0 1 3 4a1 1 0 0 1 1-1h3.5a1 1 0 0 1 1 1c0 1.25.2 2.45.57 3.57a1 1 0 0 1-.25 1z"/></svg>
      <span>614-502-7738</span>
    </li>
    <li class="contact__item">
      <svg class="contact__icon" viewBox="0 0 24 24" aria-hidden="true"><circle cx="12" cy="12" r="11" fill="var(--orange)"/><path d="M7 6c2 1 3 3 2 5s1 3 3 3-1 4-2 6M15 4c0 2 2 3 4 3M14 12c2 0 3 2 5 2" stroke="var(--white)" stroke-width="1.6" fill="none"/></svg>
      <span>skylarkreelworks.example</span>
    </li>
  </ul>

  <div class="credentials">
    <p class="credentials__cert">NRD Certified Remote Pilot</p>
    <p class="credentials__insured">FULLY INSURED</p>
  </div>

  <div class="person">
    <p class="person__name">Owen Tarrick</p>
    <p class="person__role">Owner</p>
  </div>
</section>

<section class="card card--back" aria-label="Business card back">
  <div class="brand">
    <div class="brand__name"><span>Skylark</span><span>Reelworks</span></div>
    <div class="brand__dot"></div>
  </div>
</section>

</body>
</html>
```